Tech business card design

We need an amazing business card design for our new business 'Pexla' a marketing tech startup based in Sydney, Australia. We provide an online marketplace for businesses to search and buy advertising media, connect with service providers and learn more about marketing. We wish to communicate 'cool tech', reliability and professionalism and design based around our logo.

Target Market(s)

Business Owners

Contact Information for Business Card

Name
Position
Email Address
Website
Phone Number

Font styles to use
Other font styles liked:
• Avenir & Avenir Next

Colors

Designer to choose colors to be used in the design.

```html
<!DOCTYPE html>
<html lang="en">
<head>
<meta charset="utf-8">
<title>Pexla Business Card</title>
<link href="https://fonts.googleapis.com/css2?family=Nunito+Sans:wght@300;400;700&display=swap" rel="stylesheet">
<style>
  :root {
    --backdrop: #1d1d1f;
    --card: #ffffff;
    --navy: #1b1a4e;
    --ink-soft: #6a6a72;
    --on-navy: #ffffff;
  }
  * { box-sizing: border-box; margin: 0; padding: 0; }
  html, body { width: 1200px; height: 892px; overflow: hidden; }
  body {
    background: var(--backdrop);
    font-family: "Nunito Sans", "Avenir Next", Avenir, sans-serif;
    position: relative;
  }
  .card {
    position: absolute;
    width: 540px;
    height: 308px;
    background: var(--card);
    box-shadow: 0 10px 30px rgba(0,0,0,.45);
    overflow: hidden;
  }
  .card--front { left: 90px; top: 100px; }
  .card--back { left: 570px; top: 484px; }

  .brand-name {
    font-weight: 700;
    color: var(--navy);
    line-height: 1;
  }
  .card--front .brand-name {
    position: absolute;
    left: 0; right: 0; top: 100px;
    text-align: center;
    font-size: 76px;
  }
  .card--front .web-address {
    position: absolute;
    left: 0; right: 0; top: 228px;
    text-align: center;
    font-size: 13px;
    font-weight: 300;
    letter-spacing: 7px;
    color: var(--ink-soft);
  }

  .card--back .brand-name {
    position: absolute;
    left: 48px; top: 170px;
    font-size: 64px;
  }
  .contact-panel {
    position: absolute;
    left: 300px; right: 0;
    top: 58px; height: 150px;
    background: var(--navy);
    border-radius: 12px 0 0 12px;
    color: var(--on-navy);
    padding: 16px 16px 0 22px;
  }
  .person-name {
    font-size: 19px;
    font-weight: 700;
    text-transform: uppercase;
    line-height: 1.1;
  }
  .person-role {
    font-size: 14px;
    font-weight: 300;
    text-transform: uppercase;
    margin-bottom: 14px;
  }
  .contact-list { list-style: none; }
  .contact-item {
    display: flex;
    align-items: center;
    gap: 9px;
    font-size: 13px;
    font-weight: 400;
    line-height: 1.5;
  }
  .contact-icon { width: 12px; height: 12px; flex: none; }
</style>
</head>
<body>
  <section class="card card--front">
    <div class="brand-name">Pexla</div>
    <div class="web-address">www.pexlamedia.com.au</div>
  </section>

  <section class="card card--back">
    <div class="contact-panel">
      <div class="person-name">Marcus Dale</div>
      <div class="person-role">Founder, Director</div>
      <ul class="contact-list">
        <li class="contact-item">
          <svg class="contact-icon" viewBox="0 0 12 12"><rect x="3" y="0.5" width="6" height="11" rx="1" fill="none" stroke="#fff" stroke-width="1.2"/><line x1="5" y1="9.5" x2="7" y2="9.5" stroke="#fff"/></svg>
          +61 (0)412 555 018
        </li>
        <li class="contact-item">
          <svg class="contact-icon" viewBox="0 0 12 12"><rect x="0.5" y="2.5" width="11" height="7" fill="#fff"/><polyline points="0.5,2.5 6,7 11.5,2.5" fill="none" stroke="#1b1a4e" stroke-width="1"/></svg>
          marcus@pexlamedia.com.au
        </li>
        <li class="contact-item">
          <svg class="contact-icon" viewBox="0 0 12 12"><circle cx="6" cy="6" r="5.5" fill="#fff"/><polygon points="4,8 5,5 8,4 7,7" fill="#1b1a4e"/></svg>
          www.pexlamedia.com.au
        </li>
      </ul>
    </div>
    <div class="brand-name">Pexla</div>
  </section>
</body>
</html>
```